Business Cards Needed for Innovative Healthcare Marketing Company

We are a marketing company focused on healthcare. Our company is all about rebranding yourself renewing your image and generating results. The phoenix stands for "reborn" or "rising" which we provide new brands for our clients we take their old brands and renew it with creativity and innovation. I am looking for a business card with color dimension. I have attached an example of a card I think has the look and feel of what I am trying to accomplish. I like that the card example has black and grey font colors, I like the font placement and the small logo, I really like the use of the colors on the right those are the colors of my logo. My logo is phoenix so maybe incorporating flames similar to that design. I would like the back a solid color maybe red with an opaque version of the logo and website. As a marketing company I am always open to creative liberty!

Target Market(s)

Doctors and business professionals.

Industry/Entity Type

Marketing

Contact Information for Business Card

Valcorne Health Care Marketing
Marla Tenwick- CEO
#(512)638-2974
email-marla@valcorne.com
website- valcorne.com

Font styles to use
Sans Serif

Colors
ec1f27
f37122
ffc214
fbed22
fbf289
f04a50

Requirements
Must have
• The logo and required information
Nice to have
• icons by the information
Should not have
• child like font

```html
<!DOCTYPE html>
<html lang="en">
<head>
<meta charset="utf-8">
<title>Valcorne Health Care Marketing – Business Cards</title>
<link href="https://fonts.googleapis.com/css2?family=Open+Sans:wght@300;400;700&display=swap" rel="stylesheet">
<style>
  :root {
    --canvas-bg: #e6e3df;
    --card-black: #111010;
    --card-orange: #f6931e;
    --brand-red: #b3262b;
    --brand-red-soft: #a8311f;
    --accent-orange: #f5a21d;
    --text-light: #ffffff;
    --rule-light: rgba(255, 255, 255, 0.85);
  }
  * { box-sizing: border-box; margin: 0; padding: 0; }
  html, body {
    width: 1200px;
    height: 900px;
    overflow: hidden;
    background: var(--canvas-bg);
    font-family: "Open Sans", Arial, sans-serif;
  }
  .stage {
    position: relative;
    width: 1200px;
    height: 900px;
  }
  .card {
    position: absolute;
    top: 295px;
    width: 540px;
    height: 310px;
    border-radius: 3px;
    box-shadow: 0 10px 26px rgba(0, 0, 0, 0.22);
    overflow: hidden;
  }
  /* Front */
  .card-front {
    left: 45px;
    background: var(--card-black);
    color: var(--text-light);
    text-align: center;
  }
  .holder-name {
    position: absolute;
    top: 44px;
    left: 0;
    right: 0;
    font-weight: 700;
    font-size: 19px;
    letter-spacing: 0.3px;
    color: var(--accent-orange);
  }
  .holder-title {
    position: absolute;
    top: 70px;
    left: 0;
    right: 0;
    font-size: 13px;
    font-weight: 400;
  }
  .brand-lockup {
    position: absolute;
    display: flex;
    align-items: center;
    gap: 12px;
  }
  .brand-mark {
    border-radius: 50%;
    background: var(--accent-orange);
    flex: none;
  }
  .brand-name {
    font-weight: 300;
    text-transform: uppercase;
    line-height: 1.15;
    text-align: left;
  }
  .card-front .brand-lockup { top: 108px; left: 120px; }
  .card-front .brand-mark { width: 46px; height: 46px; }
  .card-front .brand-name {
    color: var(--brand-red);
    font-size: 24px;
    letter-spacing: 1px;
    width: 270px;
  }
  .contact-icons {
    position: absolute;
    top: 196px;
    left: 0;
    right: 0;
    display: flex;
    justify-content: center;
    gap: 8px;
  }
  .contact-icons svg { width: 14px; height: 14px; }
  .contact-list {
    position: absolute;
    top: 214px;
    left: 0;
    right: 0;
    list-style: none;
    font-size: 15px;
    line-height: 20px;
  }
  /* Back */
  .card-back {
    left: 615px;
    background: var(--card-orange);
  }
  .card-back .brand-lockup { top: 92px; left: 140px; }
  .card-back .brand-mark {
    width: 50px; height: 50px;
    background: var(--brand-red-soft);
    opacity: 0.85;
  }
  .card-back .brand-name {
    color: var(--brand-red-soft);
    font-size: 25px;
    letter-spacing: 1px;
    width: 270px;
  }
  .back-rule {
    position: absolute;
    top: 240px;
    left: 0;
    right: 0;
    display: flex;
    align-items: center;
    gap: 10px;
  }
  .back-rule::before, .back-rule::after {
    content: "";
    flex: 1;
    height: 1px;
    background: var(--rule-light);
  }
  .back-website {
    color: var(--text-light);
    font-weight: 700;
    font-size: 13px;
  }
</style>
</head>
<body>
<main class="stage">
  <section class="card card-front" aria-label="Business card front">
    <p class="holder-name">MARLA TENWICK</p>
    <p class="holder-title">CEO</p>
    <div class="brand-lockup">
      <span class="brand-mark"></span>
      <span class="brand-name">Valcorne Health Care Marketing</span>
    </div>
    <div class="contact-icons" aria-hidden="true">
      <svg viewBox="0 0 16 16"><path fill="#f5a21d" d="M3 2l3 0 1 3-2 1.5c.8 1.8 2.2 3.2 4 4L10.5 9l3 1v3c0 .6-.4 1-1 1C7 14 2 9 2 3c0-.6.4-1 1-1z"/></svg>
      <svg viewBox="0 0 16 16"><rect x="1.5" y="3.5" width="13" height="9" fill="#f5a21d"/><path d="M1.5 3.5L8 9l6.5-5.5" fill="none" stroke="#111010" stroke-width="1.2"/></svg>
      <svg viewBox="0 0 16 16"><circle cx="8" cy="8" r="6.5" fill="#f5a21d"/><path d="M1.5 8h13M8 1.5c-2.5 3-2.5 10 0 13M8 1.5c2.5 3 2.5 10 0 13" fill="none" stroke="#111010" stroke-width="1"/></svg>
    </div>
    <ul class="contact-list">
      <li>(512)638-2974</li>
      <li>marla@valcorne.com</li>
      <li>www.valcorne.com</li>
    </ul>
  </section>

  <section class="card card-back" aria-label="Business card back">
    <div class="brand-lockup">
      <span class="brand-mark"></span>
      <span class="brand-name">Valcorne Health Care Marketing</span>
    </div>
    <div class="back-rule">
      <span class="back-website">www.valcorne.com</span>
    </div>
  </section>
</main>
</body>
</html>
```